RWT Fittings Ltd Business Cards

We need a business card with our business logo. We provide window and door installations on high-rises in west coast British Colombia, Canada.

I would like my business information and details on one side of the card, and the other side the company name with logo

Target Market(s)

General Contractors

Industry/Entity Type

Construction

Contact Information for Business Card

one side i want my company name and logo in the dark theme logo that i provided

Requirements
Must have
• Marco Peltieri, 16045518293, RWTFittings@mailbox-demo.com, 1407-5194 Linden Row Burnaby BC, V5H 2K9, Owner & Manager

```html
<!DOCTYPE html>
<html lang="en">
<head>
<meta charset="utf-8">
<title>RWT Fittings Ltd – Business Cards</title>
<link rel="stylesheet" href="https://fonts.googleapis.com/css2?family=Roboto:wght@400;500;700&display=swap">
<style>
  :root {
    --page-bg: #232323;
    --card-front: #1f2125;
    --card-back-dark: #25221f;
    --card-back-mid: #4a4540;
    --brand-blue: #29a6e3;
    --name-grey: #a7a9ac;
    --text-light: #e9ecef;
    --text-muted: #c9ccd0;
  }
  * { box-sizing: border-box; margin: 0; padding: 0; }
  html, body {
    width: 1200px;
    height: 780px;
    overflow: hidden;
    background: var(--page-bg);
    font-family: "Roboto", Arial, sans-serif;
  }
  .canvas {
    position: relative;
    width: 1200px;
    height: 780px;
    display: flex;
    align-items: center;
    justify-content: center;
    gap: 40px;
  }
  .card {
    position: relative;
    width: 540px;
    height: 309px;
    overflow: hidden;
    box-shadow: 0 18px 40px rgba(0, 0, 0, 0.55);
  }

  /* Contact side */
  .card-front { background: var(--card-front); }
  .brand-mark {
    position: absolute;
    display: flex;
    align-items: center;
    gap: 10px;
    font-weight: 700;
    color: var(--brand-blue);
    white-space: nowrap;
  }
  .brand-mark .brand-square {
    display: block;
    background: var(--brand-blue);
  }
  .card-front .brand-mark { top: 34px; left: 40px; font-size: 28px; }
  .card-front .brand-square { width: 22px; height: 22px; }

  .contact-list {
    position: absolute;
    left: 40px;
    top: 120px;
    list-style: none;
    color: var(--text-light);
    font-size: 13px;
    line-height: 1.45;
  }
  .contact-list li { display: flex; align-items: flex-start; gap: 8px; }
  .contact-list .address { padding-left: 22px; margin-bottom: 6px; }
  .contact-list svg { width: 14px; height: 14px; margin-top: 2px; flex: none; }

  .person {
    position: absolute;
    right: 56px;
    bottom: 44px;
    text-align: right;
  }
  .person-name {
    font-size: 26px;
    font-weight: 700;
    letter-spacing: 0.3px;
  }
  .person-name .first { color: var(--brand-blue); }
  .person-name .last { color: var(--name-grey); }
  .person-role {
    margin-top: 2px;
    font-size: 14px;
    color: var(--text-light);
  }
  .accent-bar {
    position: absolute;
    right: 0;
    bottom: 40px;
    width: 24px;
    height: 58px;
    background: var(--brand-blue);
  }

  /* Logo side */
  .card-back { background: var(--card-back-dark); }
  .backdrop {
    position: absolute;
    inset: 0;
    background:
      radial-gradient(ellipse at 65% 40%, rgba(140, 130, 120, 0.45), transparent 60%),
      linear-gradient(120deg, var(--card-back-dark) 0%, var(--card-back-mid) 55%, #5b5650 100%);
  }
  .card-back .brand-mark {
    top: 50%;
    left: 50%;
    transform: translate(-50%, -50%);
    font-size: 40px;
    gap: 14px;
  }
  .card-back .brand-square { width: 30px; height: 30px; }
</style>
</head>
<body>
<main class="canvas">

  <section class="card card-front" aria-label="Business card, contact side">
    <div class="brand-mark"><span class="brand-square"></span><span>RWT Fittings Ltd</span></div>

    <ul class="contact-list">
      <li class="address">1407-5194 Linden Row<br>Burnaby BC, V5H 2K9</li>
      <li>
        <svg viewBox="0 0 24 24" aria-hidden="true"><path fill="var(--brand-blue)" d="M6.6 10.8a15.1 15.1 0 0 0 6.6 6.6l2.2-2.2a1 1 0 0 1 1-.25 11.4 11.4 0 0 0 3.6.57 1 1 0 0 1 1 1V20a1 1 0 0 1-1 1A17 17 0 0 1 3 4a1 1 0 0 1 1-1h3.5a1 1 0 0 1 1 1c0 1.25.2 2.45.57 3.57a1 1 0 0 1-.25 1z"/></svg>
        <span>1604 551 8293</span>
      </li>
      <li>
        <svg viewBox="0 0 24 24" aria-hidden="true"><rect x="2" y="5" width="20" height="14" rx="2" fill="var(--brand-blue)"/><path d="M3 6l9 7 9-7" fill="none" stroke="var(--card-front)" stroke-width="2"/></svg>
        <span>RWTFittings@mailbox-demo.com</span>
      </li>
    </ul>

    <div class="person">
      <p class="person-name"><span class="first">Marco</span> <span class="last">Peltieri</span></p>
      <p class="person-role">Owner &amp; Manager</p>
    </div>
    <span class="accent-bar"></span>
  </section>

  <section class="card card-back" aria-label="Business card, logo side">
    <div class="backdrop" role="img" aria-label="Soft blurred photo of a bright interior with a window and plants"></div>
    <div class="brand-mark"><span class="brand-square"></span><span>RWT Fittings Ltd</span></div>
  </section>

</main>
</body>
</html>
```